Brochure required

Looking at getting business brochure designed for my solar sales company. i will require a range of products to be listed on the brochure I require a simple/ elegent / professional looking brochure.

I am happy to provide designer with all the required information that must go into the brochure. otherwise please visit www.quillebartow.com.au and view the products which i would like to allocate into the brochure aswell as our company logo and a little about me section

```html
<!DOCTYPE html>
<html lang="en">
<head>
<meta charset="utf-8">
<title>Quillebartow — Solar Brochure</title>
<link rel="stylesheet" href="https://fonts.googleapis.com/css2?family=Montserrat:wght@300;400;500;600;700&family=Rubik:wght@700;800&display=swap">
<style>
  :root{
    --bg:#e4dad4;
    --paper:#ffffff;
    --ink:#1d1d1f;
    --body:#4a4d52;
    --muted:#6b6f75;
    --teal:#1fae9a;
    --green:#25b98a;
    --blue:#1e86b8;
    --shadow:rgba(60,40,30,.18);
  }
  *{box-sizing:border-box;margin:0;padding:0}
  html,body{width:1200px;height:2440px;overflow:hidden}
  body{background:var(--bg);font-family:"Montserrat",Arial,sans-serif;color:var(--body);position:relative}

  .page{position:absolute;background:var(--paper);overflow:hidden;box-shadow:0 10px 30px var(--shadow)}
  .page svg.art{position:absolute;inset:0;width:100%;height:100%}

  /* cover */
  .cover{width:560px;height:792px}
  .cover-frame{position:absolute}
  .cover-frame--single{left:320px;top:30px;width:560px;height:792px}
  .cover-frame--spread{left:600px;top:860px;width:500px;height:707px}
  .cover-frame--spread .cover{transform:scale(.8929);transform-origin:0 0}

  .brand{position:absolute;display:flex;align-items:center;gap:10px}
  .brand-mark{width:24px;height:24px;background:var(--teal)}
  .brand-name{font-family:"Montserrat",Arial,sans-serif;font-weight:600;color:var(--ink);font-size:28px;letter-spacing:.2px;line-height:1}
  .brand-tag{position:absolute;font-size:10px;color:var(--muted);letter-spacing:.4px;white-space:nowrap}
  .cover .brand{left:50px;top:478px}
  .cover .brand-tag{left:86px;top:512px}

  .headline{position:absolute;left:50px;top:548px;font-family:"Rubik",Arial,sans-serif;font-weight:800;text-transform:uppercase;line-height:1;white-space:nowrap}
  .headline-top{display:block;font-size:31px;color:var(--ink);letter-spacing:.3px}
  .headline-main{display:block;font-size:46px;color:var(--green);margin-top:6px;letter-spacing:.3px}
  .cover .site{position:absolute;left:52px;top:730px;font-size:13px;letter-spacing:3px;color:#333}

  /* back cover */
  .back{left:100px;top:860px;width:500px;height:707px}
  .back .brand{left:48px;top:392px}
  .back .brand-name{font-size:22px}
  .back .brand-mark{width:20px;height:20px}
  .back .brand-tag{left:78px;top:420px;font-size:9px}
  .call{position:absolute;left:48px;top:470px}
  .call-label{display:block;font-weight:300;font-size:22px;color:var(--ink);letter-spacing:1px}
  .call-number{display:block;font-weight:700;font-size:28px;color:var(--blue);letter-spacing:1px;margin-top:2px}
  .back-site{position:absolute;left:48px;top:560px;display:flex;align-items:center;gap:8px;font-size:12px;color:#333;letter-spacing:1px}
  .back-site i{width:10px;height:10px;border-radius:50%;background:var(--teal);display:block}

  .spine{position:absolute;top:0;bottom:0;width:40px;pointer-events:none}
  .spine--left{right:0;background:linear-gradient(90deg,transparent,rgba(0,0,0,.07))}
  .spine--right{left:0;background:linear-gradient(270deg,transparent,rgba(0,0,0,.07))}

  /* inner spread */
  .inner-left{left:100px;top:1620px;width:500px;height:707px}
  .inner-right{left:600px;top:1620px;width:500px;height:707px}
  .product{position:absolute}
  .product-title{font-weight:600;font-size:14px;color:var(--blue);margin-bottom:6px;line-height:1.2}
  .product-title--caps{text-transform:uppercase;letter-spacing:.5px}
  .product p{font-size:10.5px;line-height:1.55;margin-bottom:8px}
  .shot{position:absolute;border-radius:4px}
  .shot--inverter{left:318px;top:40px;width:140px;height:150px;background:linear-gradient(160deg,#f4f5f6,#c9ccd0);border-radius:10px}
  .shot--optimiser{left:34px;top:215px;width:150px;height:110px;background:linear-gradient(150deg,#4a4c50,#26282b)}
  .shot--bifacial{left:345px;top:150px;width:115px;height:150px;background:linear-gradient(150deg,#3a3c3a,#161816)}
  .shot--module{left:42px;top:400px;width:140px;height:150px;background:linear-gradient(160deg,#5d8fdc,#23488f)}
</style>
</head>
<body>

<!-- Front cover -->
<div class="cover-frame cover-frame--single">
  <section class="page cover">
    <svg class="art" viewBox="0 0 560 792" preserveAspectRatio="none">
      <defs>
        <linearGradient id="coverSky" x1="0" y1="0" x2="0" y2="1">
          <stop offset="0" stop-color="#2f7fd0"/>
          <stop offset=".32" stop-color="#b7d6f2"/>
          <stop offset=".45" stop-color="#3d69b4"/>
          <stop offset="1" stop-color="#1c3468"/>
        </linearGradient>
      </defs>
      <path d="M0 0H560V276C420 286 190 330 0 470Z" fill="var(--teal)"/>
      <path d="M0 0H560V256C420 264 180 304 0 446Z" fill="url(#coverSky)" role="img" aria-label="Photo of rooftop solar panels under a blue sky with clouds"/>
    </svg>
    <div class="brand"><span class="brand-mark"></span><span class="brand-name">Quillebartow</span></div>
    <span class="brand-tag">energy solutions for a changing world</span>
    <h1 class="headline"><span class="headline-top">Energy solutions for a</span><span class="headline-main">Changing world</span></h1>
    <span class="site">www.quillebartow.com.au</span>
  </section>
</div>

<!-- Back cover -->
<section class="page back">
  <svg class="art" viewBox="0 0 500 707" preserveAspectRatio="none">
    <defs>
      <linearGradient id="backScene" x1="0" y1="0" x2="0" y2="1">
        <stop offset="0" stop-color="#7f9dbf"/>
        <stop offset=".35" stop-color="#e9c9a4"/>
        <stop offset=".5" stop-color="#8fa6b5"/>
        <stop offset="1" stop-color="#4f7a4a"/>
      </linearGradient>
    </defs>
    <path d="M0 0H500C486 190 330 300 0 332Z" fill="var(--teal)"/>
    <path d="M0 0H488C472 178 320 282 0 314Z" fill="url(#backScene)" role="img" aria-label="Photo of a solar farm in fields with a city skyline at sunset"/>
    <path d="M330 707C380 520 430 320 500 210" fill="none" stroke="var(--teal)" stroke-width="3"/>
  </svg>
  <div class="brand"><span class="brand-mark"></span><span class="brand-name">Quillebartow</span></div>
  <span class="brand-tag">energy solutions for a changing world</span>
  <div class="call"><span class="call-label">CALL US NOW</span><span class="call-number">0400-555-218</span></div>
  <div class="back-site"><i></i>www.quillebartow.com.au</div>
  <span class="spine spine--left"></span>
</section>

<!-- Front cover in spread -->
<div class="cover-frame cover-frame--spread">
  <section class="page cover">
    <svg class="art" viewBox="0 0 560 792" preserveAspectRatio="none">
      <defs>
        <linearGradient id="coverSky2" x1="0" y1="0" x2="0" y2="1">
          <stop offset="0" stop-color="#2f7fd0"/>
          <stop offset=".32" stop-color="#b7d6f2"/>
          <stop offset=".45" stop-color="#3d69b4"/>
          <stop offset="1" stop-color="#1c3468"/>
        </linearGradient>
      </defs>
      <path d="M0 0H560V276C420 286 190 330 0 470Z" fill="var(--teal)"/>
      <path d="M0 0H560V256C420 264 180 304 0 446Z" fill="url(#coverSky2)" role="img" aria-label="Photo of rooftop solar panels under a blue sky with clouds"/>
    </svg>
    <div class="brand"><span class="brand-mark"></span><span class="brand-name">Quillebartow</span></div>
    <span class="brand-tag">energy solutions for a changing world</span>
    <h1 class="headline"><span class="headline-top">Energy solutions for a</span><span class="headline-main">Changing world</span></h1>
    <span class="site">www.quillebartow.com.au</span>
    <span class="spine spine--right"></span>
  </section>
</div>

<!-- Inner spread: left page -->
<section class="page inner-left">
  <svg class="art" viewBox="0 0 500 707" preserveAspectRatio="none">
    <defs>
      <linearGradient id="fieldPhoto" x1="0" y1="0" x2="0" y2="1">
        <stop offset="0" stop-color="#c8d9ee"/>
        <stop offset=".4" stop-color="#8fa9d8"/>
        <stop offset="1" stop-color="#3f66b0"/>
      </linearGradient>
    </defs>
    <path d="M0 486C170 450 340 448 500 470V707H0Z" fill="var(--teal)"/>
    <path d="M0 500C170 464 340 462 500 484V707H0Z" fill="url(#fieldPhoto)" role="img" aria-label="Photo of ground-mounted solar panel rows under a pale sky"/>
  </svg>
  <div class="product" style="left:40px;top:40px;width:260px">
    <h2 class="product-title">Solvara Vanta 5.0-1 Inverter</h2>
    <p>The Vanta is one of the newest additions to the range. It offers smart features, Wi-Fi links, free monitoring and up to 97.8% peak efficiency. This single phase string inverter suits homes and small commercial systems from 3kW to 8kW.</p>
  </div>
  <div class="shot shot--inverter" role="img" aria-label="Product photo of a white string inverter"></div>
  <div class="shot shot--optimiser" role="img" aria-label="Product photo of a black module optimiser"></div>
  <div class="product" style="left:205px;top:215px;width:260px">
    <h2 class="product-title">Tarnel Optimiser</h2>
    <p>The Tarnel TR-4 Optimiser is a retrofit unit that brings smart module functions to standard PV panels. It can be paired with new or existing systems, giving module-level power electronics that are flexible, placeable and easy to upgrade.</p>
    <p>The company was founded in 2007. By maximising the output of each module, it solves a range of issues that limit the efficiency and safety of today's solar installations.</p>
  </div>
  <span class="spine spine--left"></span>
</section>

<!-- Inner spread: right page -->
<section class="page inner-right">
  <div class="product" style="left:40px;top:60px;width:285px">
    <h2 class="product-title product-title--caps">Duolite Bifold-DL6B.02<br>Solar Panel</h2>
    <p>Duolite Bifold absorbs solar radiation from both sides, with a bifacial rate up to 70%. Paired with a tracker, you could raise the return on your investment and lower your LCOE.</p>
    <p>Duolite Bifold is ideal for utility, farm and fishery projects. Its glass build gives better protection against PID, micro-cracking, warping, UV aging and salt mist.</p>
  </div>
  <div class="shot shot--bifacial" role="img" aria-label="Product photo of a dark bifacial solar panel"></div>
  <div class="shot shot--module" role="img" aria-label="Product photo of a blue polycrystalline solar panel"></div>
  <div class="product" style="left:210px;top:400px;width:255px">
    <h2 class="product-title">Kestra 270W Solar Panel</h2>
    <p>The Kestra Halo Series is a PID-free module suited to all kinds of installations, and it is ideal in hot, humid climates where reliability matters most.</p>
    <p>This panel sets a new standard of reliability and performance, with power classes of up to 275Wp in a 60-cell format.</p>
  </div>
  <span class="spine spine--right"></span>
</section>

</body>
</html>
```